Brell Stone Company Business Cards

Front and Back Business Card - logo and text setup - cool design. I need workable photoshop or illustrator files so I can setup each employee card with design that is created
Updates

Hi everyone, thank you for the great entries. Please no more white and blue cards - there are so many already - black and silver only now please. thanks!

Target Market(s)

Construction Industry - Facility Managers

Industry/Entity Type

Construction

Contact Information for Business Card

I really like contemporary simplistic looks - clean neat....not opposed to seeing some black backrounds

Requirements
Must have
• Logo/website address with design on front only - www.brellstone-example.com (logo attached)
• Back:
• Name/Title/Company Address/Phone/email address
Nice to have
• Cool design
Should not have
• Nothing gimmicky like Fire or Water - since we are a Fire Protection company - it has all been done

```html
<!DOCTYPE html>
<html lang="en">
<head>
<meta charset="utf-8">
<title>Brell Stone Company – Business Cards</title>
<link rel="stylesheet" href="https://fonts.googleapis.com/css2?family=Lato:wght@400;700;900&display=swap">
<style>
  :root {
    --backdrop: #5b5b5b;
    --silver-light: #e6e7e9;
    --silver-dark: #c6c8cb;
    --silver-ink: #c9cbce;
    --black: #161616;
    --ink: #1c1c1c;
    --accent: #7b7f85;
    --text-grey: #3f4246;
    --divider: #a9abaf;
  }
  * { margin: 0; padding: 0; box-sizing: border-box; }
  html, body { width: 1200px; height: 802px; overflow: hidden; }
  body {
    background: var(--backdrop);
    font-family: "Lato", sans-serif;
    position: relative;
  }
  .card {
    position: absolute;
    top: 274px;
    width: 442px;
    height: 265px;
    box-shadow: 3px 4px 8px rgba(0,0,0,0.45);
  }
  .card-back {
    left: 136px;
    background: linear-gradient(135deg, var(--silver-light), var(--silver-dark));
  }
  .card-front { left: 624px; background: var(--black); }

  .wordmark {
    position: absolute;
    font-family: "Lato", sans-serif;
    font-weight: 900;
    white-space: nowrap;
    letter-spacing: -0.5px;
  }
  .card-back .wordmark {
    left: 44px; top: 112px;
    font-size: 31px;
    line-height: 38px;
    color: var(--ink);
  }
  .card-front .wordmark {
    left: 0; right: 0; top: 88px;
    text-align: center;
    font-size: 46px;
    line-height: 54px;
    color: var(--silver-ink);
  }

  .divider {
    position: absolute;
    left: 231px; top: 65px;
    width: 1px; height: 133px;
    background: var(--divider);
  }
  .contact {
    position: absolute;
    left: 245px; top: 80px;
    color: var(--text-grey);
  }
  .person-name {
    font-size: 17px;
    font-weight: 400;
    color: var(--ink);
    line-height: 20px;
    letter-spacing: -0.2px;
  }
  .person-name .surname { color: var(--accent); }
  .person-title { font-size: 13px; line-height: 16px; }
  .contact-list { list-style: none; margin-top: 5px; font-size: 12.5px; line-height: 16px; }
  .contact-list li { display: flex; align-items: center; gap: 5px; }
  .contact-list svg { width: 9px; height: 9px; fill: var(--ink); flex: none; }
  .address { margin-top: 5px; font-size: 12.5px; line-height: 16px; padding-left: 2px; }

  .website {
    position: absolute;
    left: 0; right: 0; top: 181px;
    text-align: center;
    font-size: 14px;
    color: #e2e3e5;
  }
</style>
</head>
<body>
  <section class="card card-back" aria-label="Business card, contact side">
    <div class="wordmark">Brell Stone</div>
    <div class="divider"></div>
    <div class="contact">
      <h1 class="person-name">DANIEL <span class="surname">HARLOW</span></h1>
      <p class="person-title">Managing Director</p>
      <ul class="contact-list">
        <li>
          <svg viewBox="0 0 10 10" aria-hidden="true"><path d="M1 3 Q5 0 9 3 L8 4.5 L6.5 3.8 L6.5 3 Q5 2.6 3.5 3 L3.5 3.8 L2 4.5 Z M2.5 5 L7.5 5 L8.5 9 L1.5 9 Z"/></svg>
          000-555 010 246
        </li>
        <li>
          <svg viewBox="0 0 10 10" aria-hidden="true"><path d="M0.5 2 H9.5 V8.5 H0.5 Z M1.3 2.7 L5 5.6 L8.7 2.7 Z" fill-rule="evenodd"/></svg>
          hello@brellstone-example.com
        </li>
      </ul>
      <p class="address">18, Quarry Lane,<br>10482, Northland</p>
    </div>
  </section>

  <section class="card card-front" aria-label="Business card, logo side">
    <div class="wordmark">Brell Stone</div>
    <p class="website">www.brellstone-example.com</p>
  </section>
</body>
</html>
```